Business Card for Multi-Brand Sportswear Company

We are looking for a business card which represents our company and the multiple brands within it.

The company: Fen Athletics (LTD)
The brands: Fen, TavaPuni, ElmStretch, Grit and Rain

Employees using these cards would be representing Fen Athletics, rather than any of the individual brands. You will see a current design within the uploaded files, to give some inspiration. The actual text of the brands is not necessary, but the logos should be on there is some format.

Our creative minds on this are stretched, so we are looking for someone to make this their own, and show us what a good business card should look like.

We may like to get these printed with spot gloss, so keep that in mind with your designs.

www.fenathletics.co.uk

Industry/Entity Type

Business

Contact Information for Business Card

Leo Pemberton-Hale
Operations Manager
(+44) 1632 960 418
Leo@fenathletics.co.uk
www.fenathletics.co.uk

Font styles to use
Sans Serif
Other font styles liked:
• Eurostile

Colors
ffffff

Requirements
Nice to have
• Dark (black) background

```html
<!DOCTYPE html>
<html lang="en">
<head>
<meta charset="utf-8">
<title>Fen Athletics — Business Card</title>
<link rel="stylesheet" href="https://fonts.googleapis.com/css2?family=Exo+2:wght@400;500;600&display=swap">
<style>
  :root {
    --backdrop: #8c8c8c;
    --card: #1f1f1f;
    --ink: #ffffff;
    --ink-soft: #e6e6e6;
    --brand-violet: #6e5a78;
    --brand-red: #d3262b;
    --brand-grey: #8f8f8f;
  }
  * { margin: 0; padding: 0; box-sizing: border-box; }
  html, body { width: 1200px; height: 854px; overflow: hidden; }
  body {
    background: var(--backdrop);
    font-family: "Exo 2", sans-serif;
    color: var(--ink);
    position: relative;
  }
  .card {
    position: absolute;
    top: 281px;
    width: 512px;
    height: 293px;
    background: var(--card);
    box-shadow: 0 6px 18px rgba(0,0,0,0.25);
  }
  .card--front { left: 69px; }
  .card--back { left: 600px; }

  .wordmark {
    position: absolute;
    font-weight: 600;
    color: var(--ink);
    white-space: nowrap;
    letter-spacing: 0.5px;
  }
  .card--front .wordmark { left: 33px; top: 62px; font-size: 32px; }
  .card--back .wordmark { left: 0; right: 0; text-align: center; top: 108px; font-size: 38px; }

  .brand-row {
    position: absolute;
    display: flex;
    align-items: center;
    white-space: nowrap;
  }
  .card--front .brand-row { left: 36px; top: 141px; gap: 8px; font-size: 9px; }
  .card--back .brand-row { left: 0; right: 0; justify-content: center; top: 228px; gap: 18px; font-size: 13px; }
  .brand {
    display: flex;
    align-items: center;
    gap: 4px;
    font-weight: 500;
  }
  .brand__dot { display: inline-block; width: 0.9em; height: 0.9em; }
  .brand--tavapuni { color: #a48fae; }
  .brand--tavapuni .brand__dot { background: var(--brand-violet); }
  .brand--grit { color: var(--brand-red); }
  .brand--fen { color: var(--ink); }
  .brand--elm { color: var(--brand-grey); }
  .brand--elm .brand__dot { border-radius: 50%; border: 1.5px solid var(--brand-grey); }

  .holder {
    position: absolute;
    right: 28px;
    text-align: right;
  }
  .holder__name { font-size: 19px; font-weight: 500; position: absolute; right: 0; top: 146px; white-space: nowrap; }
  .holder__role { font-size: 15px; font-weight: 400; color: var(--ink-soft); position: absolute; right: 0; top: 178px; white-space: nowrap; }

  .contact {
    position: absolute;
    left: 45px;
    top: 202px;
    list-style: none;
    font-size: 14px;
    color: var(--ink-soft);
  }
  .contact__item { display: flex; align-items: center; height: 24px; gap: 10px; }
  .contact__icon { width: 13px; height: 13px; flex: none; }
</style>
</head>
<body>
  <section class="card card--front" aria-label="Business card front">
    <div class="wordmark">Fen Athletics</div>
    <div class="brand-row">
      <span class="brand brand--tavapuni"><i class="brand__dot"></i>TavaPuni</span>
      <span class="brand brand--grit">Grit and Rain</span>
      <span class="brand brand--fen">Fen</span>
      <span class="brand brand--elm"><i class="brand__dot"></i>ElmStretch</span>
    </div>
    <div class="holder">
      <p class="holder__name">Leo Pemberton-Hale</p>
      <p class="holder__role">Operations Manager</p>
    </div>
    <ul class="contact">
      <li class="contact__item">
        <svg class="contact__icon" viewBox="0 0 16 16" fill="none" stroke="currentColor" stroke-width="1.4"><path d="M4 2l2.5 3-1.5 2c1 2 2 3 4 4l2-1.5 3 2.5-1.5 2C8 14 2 8 2 3.5z"/></svg>
        <span>(+44) 1632 960 418</span>
      </li>
      <li class="contact__item">
        <svg class="contact__icon" viewBox="0 0 16 16" fill="none" stroke="currentColor" stroke-width="1.4"><rect x="1.5" y="3" width="13" height="10"/><path d="M1.5 3l6.5 5.5L14.5 3"/></svg>
        <span>Leo@fenathletics.co.uk</span>
      </li>
      <li class="contact__item">
        <svg class="contact__icon" viewBox="0 0 16 16" fill="none" stroke="currentColor" stroke-width="1.3"><circle cx="8" cy="8" r="6.5"/><ellipse cx="8" cy="8" rx="3" ry="6.5"/><path d="M1.5 8h13M2.5 4.5h11M2.5 11.5h11"/></svg>
        <span>www.fenathletics.co.uk</span>
      </li>
    </ul>
  </section>

  <section class="card card--back" aria-label="Business card back">
    <div class="wordmark">Fen Athletics</div>
    <div class="brand-row">
      <span class="brand brand--tavapuni"><i class="brand__dot"></i>TavaPuni</span>
      <span class="brand brand--grit">Grit and Rain</span>
      <span class="brand brand--fen">Fen</span>
      <span class="brand brand--elm"><i class="brand__dot"></i>ElmStretch</span>
    </div>
  </section>
</body>
</html>
```